Commercial Cleaning Company Website Design

We are working with Harbor Tidy Team. They are a commercial cleaning company that needs a new website design.

Some sites to use for inspiration:

https://www.plenvask.com
https://gleam-panecare.com
https://tidwellhelpers.net
https://quietnesthouse.com
https://www.thedustingbureau.com
https://www.pennytidy.com

Thank you for taking the time to consider designing a website for us. We are web developers based in Stockton and Los Angeles, CA, USA. Most of our projects go through the same process. Understanding this process may help you win a project with us. We custom-code all of our websites in-house. We don’t have any requirements as to what tools you use for your design, but we prefer Figma files. For any design that we label as four-stars, we send it to the client for review. The client picks the final design they want us to use. Once we complete this process, we will continue to show additional clients all the four-star sites and purchase them later. Your designs will have multiple chances to sell. For better chances of success, we ask that you follow these guidelines.

IMAGES:
If you use any images or icons in the design, we ask that you have a link to the asset so we can purchase the image/icon. Most of the designs we submit do not have the customer’s images on them unless they have some great images. Be creative; show us the feeling you are trying to portray with your image choices. Use any royalty-free site you choose. We subscribe to Adobe and mainly use their images, but we can purchase images outside of Adobe.

PLEASE NOTE: we will not submit designs to clients with watermarks on the images.

FONTS:
We ask that you identify the fonts used in the design. This can be done in a message if you want. We typically use Google Fonts and Adobe Fonts.

CONTENT:
We're always open to different content and ideas. We often submit designs with stock images so the client can see our vision. We typically take pictures after the website launch to use their images with our vision. Lorem Ipsum is fine for paragraphs, but we ask that you write the headers in correct English. We want to be able to show the vision and identify the sections of the website.

INSPIRATION:
We typically add a couple of links in the brief of websites we like to help you get started in your design.

REVISIONS:
We do not often ask for revisions of the designs unless we see something in the design that may not appeal to the client. If there are slight changes that we want to make, we do that in the development process.

FEEDBACK:
We rarely give feedback on designs during the design process. We are working on many website projects and do not have the time to provide feedback. We usually respond if your request is well thought out and asks specific questions, but a note asking “feedback, please” usually goes unanswered.

```html
<!DOCTYPE html>
<html lang="en">
<head>
<meta charset="utf-8">
<title>Harbor Tidy Team – Commercial Cleaning</title>
<link rel="stylesheet" href="https://fonts.googleapis.com/css2?family=Fredoka:wght@500;600&family=Roboto:ital,wght@0,400;0,500;0,700;1,400&display=swap">
<style>
:root{
  --blue:#1a3cb4;
  --blue-dark:#142f98;
  --red:#e0202a;
  --red-deep:#c8141c;
  --orange:#f7851a;
  --yellow:#fbc21e;
  --cream:#fdfbe8;
  --pale-blue:#e3eafc;
  --text:#555;
  --white:#fff;
}
*{margin:0;padding:0;box-sizing:border-box}
html,body{width:1200px;height:5164px;overflow:hidden}
body{position:relative;font-family:"Roboto",Arial,sans-serif;color:var(--text);background:var(--white)}
.abs{position:absolute}
.heading{font-family:"Fredoka","Arial Rounded MT Bold",sans-serif;font-weight:600;letter-spacing:2px;text-transform:uppercase}
.btn{position:absolute;display:flex;align-items:center;justify-content:center;font-weight:700;font-size:15px;color:var(--white);border-radius:6px;text-transform:uppercase;letter-spacing:.3px}
.btn-red{background:var(--red);box-shadow:0 3px 0 var(--red-deep)}
.photo{position:absolute}

/* top bar */
.topbar{top:0;left:0;width:1200px;height:36px}
.topbar .oncall{left:380px;top:10px;font-size:12px;color:#333;display:flex;gap:8px;align-items:center}
.topbar .band{left:720px;top:0;width:480px;height:36px;background:var(--blue)}
.topbar .call{left:738px;top:0;width:270px;height:40px;background:var(--red);clip-path:polygon(4% 0,100% 0,96% 100%,0 100%);display:flex;align-items:center;justify-content:center;gap:10px;color:#fff;font-size:15px;font-weight:500}
.call .dot{width:26px;height:26px;border-radius:50%;background:#fff;display:flex;align-items:center;justify-content:center}

/* header */
.logo{left:140px;top:58px;display:flex;align-items:center;gap:12px}
.logo .mark{width:26px;height:26px;background:var(--red);border-radius:4px}
.logo .name{font-family:"Fredoka",sans-serif;font-weight:600;font-size:30px;color:var(--blue);letter-spacing:3px}
.nav{left:582px;top:82px;display:flex;gap:32px;font-size:14px;font-weight:500;color:#222}

/* hero */
.hero{top:132px;left:0;width:1200px;height:628px}
.hero-red{left:400px;top:132px;width:800px;height:610px;background:linear-gradient(120deg,#d61c24,#ee3a3a 60%,#e52a2a);clip-path:polygon(245px 0,100% 0,100% 100%,0 100%)}
.hero-photo{left:0;top:132px;width:650px;height:628px;background:linear-gradient(135deg,#c9cdd2,#8d98a8 45%,#2f4a8a 70%,#e8d38c);clip-path:polygon(0 0,100% 0,370px 100%,0 100%)}
.hero-title{left:590px;top:326px;color:#fff;font-size:34px;line-height:53px}
.hero-sub{left:590px;top:454px;color:#fff;font-size:17px}
.hero .b1{left:590px;top:510px;width:200px;height:46px;background:var(--blue);box-shadow:0 3px 0 #0f2676;font-size:14px}
.hero .b2{left:806px;top:510px;width:200px;height:46px;background:var(--yellow);box-shadow:0 3px 0 #d39a0a;font-size:14px}
.dots{left:590px;top:614px;display:flex;gap:20px}
.dots span{width:9px;height:9px;border-radius:50%;background:#fff}
.dots span.on{background:var(--yellow)}

/* section titles */
.sec-title{left:0;width:1200px;text-align:center;font-size:52px;color:var(--blue)}

/* services */
.svc{top:1000px;width:134px;height:540px;border-radius:12px;overflow:hidden}
.svc .label{position:absolute;left:50%;bottom:160px;transform:translateX(-50%) rotate(-90deg);transform-origin:center;white-space:nowrap;color:#fff;font-weight:700;font-size:24px;width:0;display:flex;justify-content:center}
.svc1{left:144px;background:linear-gradient(180deg,#1e3fbd,#152a6c 60%,#0c1a48)}
.svc2{left:292px;background:linear-gradient(180deg,#d9a23a,#6e3a10 50%,#c27a22)}
.svc3{left:440px;background:linear-gradient(180deg,#d73324,#8e1a12 55%,#b3361c)}
.specialty{left:586px;top:1000px;width:466px;height:540px;background:var(--pale-blue);border-radius:12px}
.specialty .pic{left:22px;top:20px;width:420px;height:270px;border-radius:10px;background:linear-gradient(180deg,#f1ece6,#9fb3cf 55%,#3b5fa8)}
.specialty h3{position:absolute;left:50px;top:322px;font-size:19px;color:#333;font-weight:700}
.specialty p{position:absolute;left:50px;top:360px;width:380px;font-size:14px;line-height:27px;color:#666}
.specialty .btn{left:50px;top:464px;width:160px;height:44px}

/* about */
.about{top:1648px;left:0;width:1200px;height:644px;background:var(--cream);overflow:hidden}
.about .wedge{right:0;top:0;width:420px;height:644px;background:linear-gradient(160deg,#fbb21f,#f47a1a 50%,#e3221f);clip-path:polygon(70% 0,100% 0,100% 100%,0 100%,8% 82%,58% 20%)}
.about h2{left:144px;top:84px;font-size:54px;color:var(--blue)}
.about p{left:144px;top:166px;width:478px;font-size:15.5px;line-height:32px;color:#666;text-align:justify}
.about .btn{left:144px;top:492px;width:160px;height:44px}
.about .ring{left:650px;top:70px;width:500px;height:500px;border-radius:50%;background:#fdf5d8}
.about .circle-photo{left:668px;top:82px;width:466px;height:466px;border-radius:50%;background:linear-gradient(160deg,#e9ecef,#a9b3bf 50%,#2a4fa6)}

/* reviews */
.review{width:268px;background:#fff;border:2px solid #e1e1e1;border-radius:10px;text-align:center}
.review .avatar{position:absolute;left:106px;top:-34px;width:56px;height:56px;border-radius:50%;background:#a9c0ef;display:flex;align-items:center;justify-content:center}
.review .who{margin-top:46px;font-size:13px;font-weight:700;color:#333}
.review .who span{color:var(--yellow);letter-spacing:1px}
.review p{margin:14px 24px 0;font-size:12.5px;line-height:25px;font-style:italic;color:#777;text-align:justify;text-align-last:center}
.review.active{border-bottom:6px solid var(--blue)}

/* why */
.why{top:3196px;left:0;width:1200px;height:660px;background:linear-gradient(180deg,#f27d12,#f8931e 50%,#f18a16)}
.why h2{left:0;top:80px;width:1200px;text-align:center;font-size:52px;color:#fff}
.why .ring{left:448px;top:240px;width:300px;height:300px;border-radius:50%;background:var(--yellow)}
.why .inner{left:486px;top:278px;width:224px;height:224px;border-radius:50%;background:#fff;display:flex;align-items:center;justify-content:center;font-family:"Fredoka",sans-serif;font-weight:600;font-size:19px;letter-spacing:2px;color:var(--blue)}
.why .ic{width:72px;height:72px;border-radius:50%;background:#fff;display:flex;align-items:center;justify-content:center;box-shadow:0 0 0 5px rgba(255,255,255,.35)}
.why .ic.red{background:var(--red)}
.feat{width:262px;color:#fff}
.feat h4{font-size:17px;font-weight:700;margin-bottom:8px}
.feat p{font-size:13.5px;line-height:26px;color:#fff3e2}
.feat.l{text-align:right}

/* gallery */
.tabs{left:466px;top:4110px;display:flex;gap:38px;font-size:13px;font-weight:700;color:#333;align-items:center}
.tabs .on{background:var(--yellow);color:#fff;padding:5px 10px;border-radius:3px}
.tile{width:222px;height:182px}

/* footer */
.footer{top:4724px;left:0;width:1200px;height:440px;background:var(--blue)}
.footer h2{left:146px;top:76px;font-size:44px;color:#fff}
.footer .btn{left:730px;top:64px;width:318px;height:44px;font-size:16px}
.footer .rule{left:146px;height:1px;width:1012px;background:rgba(255,255,255,.25)}
.fnav{left:0;top:190px;width:1200px;display:flex;justify-content:center;gap:38px;color:#fff;font-size:17px;font-weight:500}
.contact{top:286px;display:flex;align-items:center;gap:16px;color:#fff;font-size:16px}
.contact .ci{width:32px;height:32px;border-radius:50%;background:#fff;display:flex;align-items:center;justify-content:center}
.contact .ci.red{background:var(--red)}
.copy{left:146px;top:380px;color:#fff;font-size:14px}
.social{left:874px;top:370px;display:flex;gap:8px}
.social span{width:30px;height:30px;border-radius:50%;border:2px solid #fff}
</style>
</head>
<body>

<!-- Top bar -->
<div class="abs topbar">
  <div class="abs oncall">
    <svg width="14" height="14" viewBox="0 0 14 14"><circle cx="7" cy="7" r="6" fill="none" stroke="#333" stroke-width="1.5"/><path d="M7 3.5V7l2.5 1.5" stroke="#333" stroke-width="1.5" fill="none"/></svg>
    ON CALL 24 HOURS A DAY. 7 DAYS A WEEK
  </div>
  <div class="abs band"></div>
  <div class="abs call">
    <span class="dot"><svg width="14" height="14" viewBox="0 0 24 24"><path fill="#e0202a" d="M6.6 10.8a15.1 15.1 0 006.6 6.6l2.2-2.2c.3-.3.7-.4 1-.2 1.1.4 2.3.6 3.6.6.6 0 1 .4 1 1V20c0 .6-.4 1-1 1A17 17 0 013 4c0-.6.4-1 1-1h3.5c.6 0 1 .4 1 1 0 1.3.2 2.5.6 3.6.1.3 0 .7-.2 1z"/></svg></span>
    CALL US : +1 888 888 8888
  </div>
</div>

<!-- Header -->
<div class="abs logo"><span class="mark"></span><span class="name">HARBOR TIDY TEAM</span></div>
<nav class="abs nav"><span>HOME</span><span>ABOUT</span><span>SERVICES</span><span>RESOURCES</span><span>CONTACT</span></nav>

<!-- Hero -->
<section class="abs hero" style="top:0;height:760px">
  <div class="abs hero-red"></div>
  <div class="photo hero-photo" role="img" aria-label="Smiling cleaner in blue uniform wiping a window with a cloth"></div>
  <h1 class="abs heading hero-title" style="font-weight:500">Commercial Cleaning.<br>Expertly Delivered.</h1>
  <p class="abs hero-sub">Serving your business with precision, reliability, and care.</p>
  <div class="btn b1">Request a Quote</div>
  <div class="btn b2">View All Services</div>
  <div class="abs dots"><span></span><span class="on"></span><span></span><span></span></div>
</section>

<!-- Services -->
<h2 class="abs heading sec-title" style="top:876px">Our Services</h2>
<div class="abs svc svc1" role="img" aria-label="Cleaner vacuuming an office at night"><span class="label">OFFICE CLEANING</span></div>
<div class="abs svc svc2" role="img" aria-label="Chef serving food in a restaurant kitchen"><span class="label">RETAIL &amp; HOSPITALITY</span></div>
<div class="abs svc svc3" role="img" aria-label="Construction worker on a building site"><span class="label">POST CONSTRUCTION</span></div>
<div class="abs specialty">
  <div class="photo pic" role="img" aria-label="Team of cleaners in uniforms with equipment"></div>
  <h3>SPECIALTY SERVICES</h3>
  <p>Sed ut perspiciatis unde omnis iste natus error sit voluptatem acc doloremque laudantium, totam rem aperiam eaque ipsa quae ab</p>
  <div class="btn btn-red">Read More</div>
</div>

<!-- About -->
<section class="abs about">
  <div class="abs wedge"></div>
  <h2 class="abs heading">About Us</h2>
  <p class="abs">Sed ut perspiciatis unde omnis iste natus error sit voluptatem accusantium doloremque laudantium, totam rem aperiam, eaque ipsa quae ab illo inventore veritatis et quasi architecto beatae vitae dicta sunt explicabo. Nemo enim ipsam voluptatem quia voluptas sit aspernatur aut odit aut fugit, sed quia consequunturSed ut perspiciatis unde omnis iste natus error sit voluptatem accusantium doloremque laudantium, totam rem aperiam, eaque ipsa quae ab illo inventore veritatis et quasi architecto beatae vitae dicta sunt explicabo.</p>
  <div class="btn btn-red">Read More</div>
  <div class="abs ring"></div>
  <div class="photo circle-photo" role="img" aria-label="Cleaner in blue overalls mopping an office floor"></div>
</section>

<!-- Reviews -->
<h2 class="abs heading sec-title" style="top:2428px">Customer Reviews</h2>
<div class="abs review" style="left:46px;top:2598px;height:310px">
  <div class="avatar"><svg width="26" height="26" viewBox="0 0 24 24" fill="#fff"><circle cx="12" cy="8" r="4.5"/><path d="M3 22c0-5 4-8 9-8s9 3 9 8z"/></svg></div>
  <div class="who">John Doe <span>★★★★★</span></div>
  <p>"Sed ut perspiciatis unde omnis iste natus error sit voluptatem accusantidoloremque laudantium, totam rem aperiam, eaque ipsa quae ab illo inventore veritatis et quasi architecto beatae vitae dicta sunt explicaboemo enim ipsam voluptatem quia voluptas"</p>
</div>
<div class="abs review active" style="left:326px;top:2662px;height:318px">
  <div class="avatar"><svg width="26" height="26" viewBox="0 0 24 24" fill="#fff"><circle cx="12" cy="8" r="4.5"/><path d="M3 22c0-5 4-8 9-8s9 3 9 8z"/></svg></div>
  <div class="who">John Doe <span>★★★★★</span></div>
  <p>"Sed ut perspiciatis unde omnis iste natus error sit voluptatem accusantidoloremque laudantium, totam rem aperiam, eaque ipsa quae ab illo inventore veritatis et quasi architecto beatae vitae dicta sunt explicaboemo enim ipsam voluptatem quia voluptas"</p>
</div>
<div class="abs review" style="left:604px;top:2598px;height:310px">
  <div class="avatar"><svg width="26" height="26" viewBox="0 0 24 24" fill="#fff"><circle cx="12" cy="8" r="4.5"/><path d="M3 22c0-5 4-8 9-8s9 3 9 8z"/></svg></div>
  <div class="who">John Doe <span>★★★★★</span></div>
  <p>"Sed ut perspiciatis unde omnis iste natus error sit voluptatem accusantidoloremque laudantium, totam rem aperiam, eaque ipsa quae ab illo inventore veritatis et quasi architecto beatae vitae dicta sunt explicaboemo enim ipsam voluptatem quia voluptas"</p>
</div>
<div class="abs review" style="left:884px;top:2662px;height:312px">
  <div class="avatar"><svg width="26" height="26" viewBox="0 0 24 24" fill="#fff"><circle cx="12" cy="8" r="4.5"/><path d="M3 22c0-5 4-8 9-8s9 3 9 8z"/></svg></div>
  <div class="who">John Doe <span>★★★★★</span></div>
  <p>"Sed ut perspiciatis unde omnis iste natus error sit voluptatem accusantidoloremque laudantium, totam rem aperiam, eaque ipsa quae ab illo inventore veritatis et quasi architecto beatae vitae dicta sunt explicaboemo enim ipsam voluptatem quia voluptas"</p>
</div>
<div class="btn btn-red" style="left:470px;top:3048px;width:260px;height:42px">View More Reviews</div>

<!-- Why choose us -->
<section class="abs why">
  <h2 class="abs heading">Why Choose Us</h2>
  <div class="abs ring"></div>
  <div class="abs inner">HARBOR TIDY TEAM</div>

  <div class="abs ic" style="left:442px;top:244px"><svg width="32" height="32" viewBox="0 0 24 24" fill="#f47a1a"><path d="M2 10l4-4 4 3 3-2 4 1 5 3-4 5-3-1-3 3-4-3-3 1z"/></svg></div>
  <div class="abs ic" style="left:682px;top:244px"><svg width="28" height="30" viewBox="0 0 24 26" fill="#f47a1a"><rect x="3" y="11" width="18" height="14" rx="2"/><path d="M7 11V7a5 5 0 0110 0v4" fill="none" stroke="#f47a1a" stroke-width="3"/></svg></div>
  <div class="abs ic red" style="left:442px;top:452px"><svg width="30" height="30" viewBox="0 0 24 24" fill="#fff"><path d="M20 3C9 3 4 9 5 17l-2 3 1.5 1 2-3C14 19 20 13 20 3z"/></svg></div>
  <div class="abs ic" style="left:682px;top:452px"><svg width="32" height="28" viewBox="0 0 28 24" fill="#f47a1a"><circle cx="14" cy="7" r="4"/><circle cx="6" cy="9" r="3"/><circle cx="22" cy="9" r="3"/><path d="M6 22c0-5 3-8 8-8s8 3 8 8zM0 20c0-4 2-6 6-6l1 .3C5 16 4.5 18 4.5 20zM28 20c0-4-2-6-6-6l-1 .3c2 1.7 2.5 3.7 2.5 5.7z"/></svg></div>

  <div class="abs feat l" style="left:148px;top:240px"><h4>RELIABILITY</h4><p>Lorem ipsum dolor sit amet, consectetur adipiscing elit sed do eiusmod tempoem ipsum dolor sit amet.</p></div>
  <div class="abs feat" style="left:788px;top:240px"><h4>SAFETY &amp; COMPLIANCE</h4><p>Lorem ipsum dolor sit amet, consectetur adipiscing elit sed do eiusmod tempoem ipsum dolor sit amet.</p></div>
  <div class="abs feat l" style="left:148px;top:462px"><h4>GREEN CLEANING</h4><p>Lorem ipsum dolor sit amet, consectetur adipiscing elit sed do eiusmod tempoem ipsum dolor sit amet.</p></div>
  <div class="abs feat" style="left:788px;top:462px"><h4>CERTIFIED TEAM</h4><p>Lorem ipsum dolor sit amet, consectetur adipiscing elit sed do eiusmod tempoem ipsum dolor sit amet.</p></div>
</section>

<!-- Gallery -->
<h2 class="abs heading sec-title" style="top:3970px">Project Gallery</h2>
<div class="abs" style="left:300px;top:4082px;width:600px;height:1px;background:#eee"></div>
<div class="abs tabs"><span class="on">ALL</span><span>FEATURED</span><span>LATEST</span></div>
<div class="photo tile" style="left:144px;top:4176px;background:linear-gradient(150deg,#b9b3aa,#5c5a56)" role="img" aria-label="Cleaner vacuuming a corridor"></div>
<div class="photo tile" style="left:374px;top:4176px;background:linear-gradient(150deg,#9a8574,#2b3b64)" role="img" aria-label="Cleaner vacuuming carpet in an office"></div>
<div class="photo tile" style="left:604px;top:4176px;background:linear-gradient(150deg,#e7ecf4,#6d8bc2)" role="img" aria-label="Gloved hands spraying a desk surface"></div>
<div class="photo" style="left:834px;top:4176px;width:222px;height:374px;background:linear-gradient(160deg,#6a5a30,#3a3420 50%,#c9a54a)" role="img" aria-label="Smiling cleaner wiping glass"></div>
<svg class="abs" style="left:925px;top:4346px" width="40" height="40" viewBox="0 0 40 40"><path d="M20 2v36M2 20h36" stroke="#fff" stroke-width="3"/></svg>
<div class="photo tile" style="left:144px;top:4368px;background:linear-gradient(150deg,#d3d0cc,#6a6560)" role="img" aria-label="Cleaner scrubbing a floor on hands and knees"></div>
<div class="photo tile" style="left:374px;top:4368px;background:linear-gradient(150deg,#4b6a86,#1f2f4a)" role="img" aria-label="Cleaner mopping by a glass wall"></div>
<div class="photo tile" style="left:604px;top:4368px;background:linear-gradient(150deg,#dadde2,#7d828a)" role="img" aria-label="Cleaner in a commercial kitchen"></div>
<div class="btn btn-red" style="left:470px;top:4620px;width:260px;height:42px">View More Projetcs</div>

<!-- Footer -->
<footer class="abs footer">
  <h2 class="abs heading" style="font-weight:500">Let Your Home Shine</h2>
  <div class="btn btn-red">Get A Free Estimate Today!</div>
  <div class="abs rule" style="top:148px"></div>
  <nav class="abs fnav"><span>HOME</span><span>ABOUT</span><span>SERVICES</span><span>RESOURCES</span><span>CONTACT</span><span>PRIVACY POLICY</span></nav>
  <div class="abs contact" style="left:150px"><span class="ci"><svg width="16" height="16" viewBox="0 0 24 24"><path fill="#1a3cb4" d="M6.6 10.8a15.1 15.1 0 006.6 6.6l2.2-2.2c.3-.3.7-.4 1-.2 1.1.4 2.3.6 3.6.6.6 0 1 .4 1 1V20c0 .6-.4 1-1 1A17 17 0 013 4c0-.6.4-1 1-1h3.5c.6 0 1 .4 1 1 0 1.3.2 2.5.6 3.6.1.3 0 .7-.2 1z"/></svg></span>Call Us : +1 888 888 8888</div>
  <div class="abs" style="left:438px;top:284px;width:1px;height:36px;background:rgba(255,255,255,.3)"></div>
  <div class="abs contact" style="left:480px"><span class="ci red"><svg width="16" height="12" viewBox="0 0 16 12"><rect width="16" height="12" rx="2" fill="#fff"/><path d="M1 1l7 6 7-6" stroke="#e0202a" fill="none" stroke-width="1.5"/></svg></span>info@companyname.com</div>
  <div class="abs" style="left:770px;top:284px;width:1px;height:36px;background:rgba(255,255,255,.3)"></div>
  <div class="abs contact" style="left:808px"><span class="ci"><svg width="14" height="18" viewBox="0 0 14 18"><path fill="#1a3cb4" d="M7 0a7 7 0 00-7 7c0 5 7 11 7 11s7-6 7-11a7 7 0 00-7-7zm0 9.5A2.5 2.5 0 117 4.5a2.5 2.5 0 010 5z"/></svg></span>123,Lorem Ipsum dolor</div>
  <div class="abs rule" style="top:350px"></div>
  <div class="abs copy">© 2025 Companyname. All rights reserved &nbsp;|&nbsp; Privacy Policy &nbsp;|&nbsp; Terms of use</div>
  <div class="abs social"><span></span><span></span><span></span><span></span><span></span></div>
</footer>

</body>
</html>
```